VFX Company Business Card Design Project

The Kestrel Works is a decentralized Visual Effects Studio servicing the television and feature film industries.
Project Brief:
Take our logo that was previously designed on Pencil Harbor and make a double sided business card.
Requirements:
- Card MUST be double sided.
- Front of card MUST have the yellow part of our logo against the dark grey background.
- Back of card is completely up to the designer.
- Back of card must include the complete company logo.
Please follow these File Preparation guidelines:
http://printnook.ca/infopage?file=filetype_en&s=PrintNook_new&lang=en
Business

```html
<!DOCTYPE html>
<html lang="en">
<head>
<meta charset="utf-8">
<title>The Kestrel Works – Business Card</title>
<link href="https://fonts.googleapis.com/css2?family=Questrial&family=Open+Sans:wght@400&display=swap" rel="stylesheet">
<style>
  :root {
    --backdrop: #e9dccb;
    --label: #2b2118;
    --card-black: #000000;
    --card-grey: #2a2a2a;
    --accent-yellow: #fdc82f;
    --text-white: #f2f2f2;
    --text-soft: #cfcfcf;
    --rule: #5a5a5a;
  }
  html, body {
    margin: 0;
    padding: 0;
    overflow: hidden;
  }
  body {
    width: 1200px;
    height: 788px;
    background: var(--backdrop);
    position: relative;
    font-family: "Questrial", "Century Gothic", sans-serif;
  }
  .side-label {
    position: absolute;
    font-family: "Open Sans", Arial, sans-serif;
    font-size: 21px;
    color: var(--label);
    transform: translateX(-50%);
    white-space: nowrap;
  }
  .card {
    position: absolute;
    width: 524px;
    height: 300px;
    border-radius: 18px;
    box-sizing: border-box;
    overflow: hidden;
  }
  .card--back { left: 338px; top: 75px; background: var(--card-black); }
  .card--front-one { left: 54px; top: 446px; background: var(--card-grey); }
  .card--front-two { left: 623px; top: 446px; background: var(--card-black); }

  .brand-name {
    position: absolute;
    font-size: 40px;
    line-height: 1;
    color: var(--text-soft);
    white-space: nowrap;
  }
  .card--back .brand-name { left: 30px; top: 52px; }

  .holder { position: absolute; right: 31px; top: 174px; text-align: right; }
  .holder__name { font-size: 20px; color: var(--text-white); letter-spacing: 1px; }
  .holder__role { font-size: 14px; color: var(--text-soft); letter-spacing: 1px; margin-top: 3px; }

  .divider {
    position: absolute; left: 30px; right: 31px; top: 222px;
    height: 1px; background: var(--rule);
  }
  .contact {
    position: absolute; top: 243px;
    font-family: "Open Sans", Arial, sans-serif;
    font-size: 12.5px; color: var(--text-white); line-height: 20px;
  }
  .contact--phones { left: 32px; }
  .contact--online { left: 178px; }
  .contact--address { right: 31px; top: 229px; text-align: right; line-height: 17px; }
  .contact__row { display: flex; align-items: center; gap: 6px; }
  .contact__row svg { width: 10px; height: 10px; }

  .mark-lockup {
    position: absolute; display: flex; align-items: center; gap: 16px;
    left: 50%; transform: translateX(-50%); white-space: nowrap;
  }
  .card--front-one .mark-lockup { top: 118px; }
  .card--front-one .brand-name { position: static; color: var(--accent-yellow); font-size: 46px; }
  .card--front-two .mark-lockup { top: 126px; }
  .card--front-two .brand-name { position: static; color: var(--text-soft); font-size: 40px; }
  .mark-dot { width: 40px; height: 40px; border-radius: 50%; background: var(--accent-yellow); flex: none; }

  .web-address {
    position: absolute; left: 0; right: 0; top: 256px;
    text-align: center; font-size: 20px; letter-spacing: 3px; color: var(--text-white);
  }
</style>
</head>
<body>
  <div class="side-label" style="left:600px; top:32px;">Back</div>
  <div class="side-label" style="left:326px; top:403px;">Front - 1</div>
  <div class="side-label" style="left:900px; top:403px;">Front - 2</div>

  <section class="card card--back">
    <div class="brand-name">The Kestrel Works</div>
    <div class="holder">
      <div class="holder__name">Your Name</div>
      <div class="holder__role">Designation</div>
    </div>
    <div class="divider"></div>
    <div class="contact contact--phones">
      <div class="contact__row">
        <svg viewBox="0 0 10 10"><path d="M2 1 L4 1 L4.5 3 L3.3 3.8 Q4.3 5.8 6.2 6.7 L7 5.5 L9 6 L9 8 Q5 9.5 1.5 5 Q0.8 3 2 1Z" fill="#bbb"/></svg>
        <span>123-456-7890</span>
      </div>
      <div class="contact__row">
        <svg viewBox="0 0 10 10"><rect x="2.5" y="0.5" width="5" height="9" rx="1" fill="#bbb"/><rect x="3.3" y="1.6" width="3.4" height="5.6" fill="#000"/></svg>
        <span>123-456-7890</span>
      </div>
    </div>
    <div class="contact contact--online">
      <div class="contact__row">
        <svg viewBox="0 0 10 10"><rect x="0.5" y="2" width="9" height="6" fill="none" stroke="#bbb"/><path d="M0.5 2 L5 5.5 L9.5 2" fill="none" stroke="#bbb"/></svg>
        <span>info@website.com</span>
      </div>
      <div class="contact__row">
        <svg viewBox="0 0 10 10"><circle cx="5" cy="5" r="4.3" fill="#bbb"/><path d="M0.7 5 H9.3 M5 0.7 Q2.5 5 5 9.3 M5 0.7 Q7.5 5 5 9.3" fill="none" stroke="#000" stroke-width="0.7"/></svg>
        <span>www.website.com</span>
      </div>
    </div>
    <div class="contact contact--address">
      <div>0000#, Area Name</div>
      <div>Street Name, State Name</div>
      <div>Country code</div>
    </div>
  </section>

  <section class="card card--front-one">
    <div class="mark-lockup">
      <span class="mark-dot"></span>
      <span class="brand-name">The Kestrel Works</span>
    </div>
    <div class="web-address">www.website.com</div>
  </section>

  <section class="card card--front-two">
    <div class="mark-lockup">
      <span class="mark-dot"></span>
      <span class="brand-name">The Kestrel Works</span>
    </div>
    <div class="web-address">www.website.com</div>
  </section>
</body>
</html>
```